A wine Label for a new brand of New Zealand Wine

We are looking for a Wine Label for our "Harbor Pine" brand of wines from North Otago New Zealand. We would like the label to perhaps use the HP as a logo and the rest up to the designer. We have our vineyards located in the Waitaki Valley New Zealand which is a southern region with mountains and a river flowing past our vineyard. Photos attached of Dramatic Landscape. Also attached is a basic outline of requirements for the front bottle of the label. The rear bottle label will contain writing about the wines background plus statutory regulations on Alc. Vol, bar code etc. Front Label size to be no Larger than 80mm deep by 100 mm wide. The label can be simple or graphic, whatever the designer chooses.
Target Market(s)
New Wine Brand
Look and feel
Each slider illustrates characteristics of the customer's brand and the style your logo design should communicate.

```html
<!DOCTYPE html>
<html lang="en">
<head>
<meta charset="utf-8">
<title>Harbor Pine — Pinot Gris Front Label</title>
<link rel="stylesheet" href="https://fonts.googleapis.com/css2?family=Cinzel:wght@700&family=Cormorant+Garamond:ital,wght@0,500;0,600;1,500&display=swap">
<style>
  :root {
    --page: #f4f4f2;
    --paper: #f7f5ec;
    --gold: #b8873c;
    --gold-light: #d9b36a;
    --ink: #2b2a27;
    --mark-ink: #151515;
  }
  * { box-sizing: border-box; margin: 0; padding: 0; }
  html, body { width: 995px; height: 1200px; overflow: hidden; }
  body {
    background: var(--page);
    position: relative;
    font-family: "Cormorant Garamond", Georgia, serif;
    color: var(--ink);
  }

  /* Brand mark tile */
  .brand-tile {
    position: absolute;
    left: 397px; top: 50px;
    width: 200px; height: 200px;
    border: 3px solid var(--mark-ink);
    display: flex; align-items: center; justify-content: center;
  }
  .brand-tile__name {
    font-family: "Cinzel", Georgia, serif;
    font-weight: 700;
    font-size: 84px;
    color: var(--mark-ink);
    letter-spacing: 2px;
  }

  /* Front label */
  .label {
    position: absolute;
    left: 197px; top: 320px;
    width: 600px; height: 750px;
    background: var(--paper);
    box-shadow: 0 2px 10px rgba(0,0,0,0.12);
  }
  .label__frame {
    position: absolute; inset: 0;
    width: 600px; height: 750px;
  }
  .label__monogram {
    position: absolute;
    left: 256px; top: 80px;
    width: 88px; height: 88px;
    border: 2px solid var(--gold);
    display: flex; align-items: center; justify-content: center;
    font-family: "Cinzel", Georgia, serif;
    font-weight: 700;
    font-size: 36px;
    color: var(--gold);
  }
  .label__brand {
    position: absolute;
    left: 0; right: 0; top: 282px;
    text-align: center;
    font-family: "Cinzel", Georgia, serif;
    font-weight: 700;
    font-size: 54px;
    letter-spacing: 2px;
    color: var(--gold);
  }
  .label__vintage {
    position: absolute;
    left: 0; right: 0; top: 480px;
    text-align: center;
    font-weight: 500;
    font-size: 24px;
    letter-spacing: 3px;
  }
  .label__varietal {
    position: absolute;
    left: 0; right: 0; top: 510px;
    text-align: center;
    font-weight: 500;
    font-size: 40px;
    letter-spacing: 6px;
    text-transform: uppercase;
  }
  .label__origin {
    position: absolute;
    left: 0; right: 0; top: 612px;
    text-align: center;
    font-style: italic;
    font-size: 24px;
  }
  .label__region {
    position: absolute;
    left: 0; right: 0; top: 650px;
    text-align: center;
    font-weight: 500;
    font-size: 17px;
    letter-spacing: 1.5px;
    text-transform: uppercase;
  }
</style>
</head>
<body>
  <div class="brand-tile">
    <span class="brand-tile__name">HP</span>
  </div>

  <section class="label">
    <svg class="label__frame" viewBox="0 0 600 750" aria-hidden="true">
      <rect x="20" y="20" width="560" height="710" fill="none" stroke="#b8873c" stroke-width="3"/>
      <rect x="29" y="29" width="542" height="692" fill="none" stroke="#d9b36a" stroke-width="1.2"/>
    </svg>
    <div class="label__monogram">HP</div>
    <h1 class="label__brand">Harbor Pine</h1>
    <p class="label__vintage">2015</p>
    <p class="label__varietal">Pinot Gris</p>
    <p class="label__origin">New Zealand Wine</p>
    <p class="label__region">Waitaki Valley—North Otago</p>
  </section>
</body>
</html>
```